Local Roofing/Construction company business needs new biz card design

We need a new business card design, current cards are from the start of this operation and generic at best. We are a local Construction Company (General Contractor) with a majority of our work originating from insurance claims-exterior finish work is the main focus (Roofs-Siding-Gutters etc). Heavily involved with homeowners and the low ball offers they receive from insurance company's after a insurable event takes place. I have attached some of our original logo file(s) below.

```html
<!DOCTYPE html>
<html lang="en">
<head>
<meta charset="utf-8">
<title>Northgate Builders – Business Card</title>
<link href="https://fonts.googleapis.com/css2?family=Montserrat:wght@400;500;700;800&display=swap" rel="stylesheet">
<style>
  :root {
    --backdrop: #1d1e22;
    --brand-green: #55bd6f;
    --brand-green-deep: #3fae5c;
    --pattern-green: #4db466;
    --card-white: #f8f5f2;
    --ink: #15191b;
    --night: #0f1e21;
  }
  * { box-sizing: border-box; margin: 0; padding: 0; }
  html, body {
    width: 1200px; height: 900px; overflow: hidden;
    background: var(--backdrop);
    font-family: "Montserrat", sans-serif;
  }
  .stage {
    width: 1200px; height: 900px;
    display: flex; flex-direction: column; align-items: center; justify-content: center;
    gap: 56px;
  }
  .card {
    position: relative;
    width: 620px; height: 354px;
    border-radius: 22px;
    overflow: hidden;
  }
  /* Front */
  .card-front { background: var(--brand-green); }
  .front-pattern {
    position: absolute; inset: 0;
    background: linear-gradient(135deg, var(--brand-green) 0%, var(--pattern-green) 100%);
  }
  .front-badge {
    position: absolute; left: 50%; top: 50%;
    transform: translate(-50%, -50%);
    width: 170px; height: 140px;
    background: #ffffff;
    border-radius: 18px;
    display: flex; align-items: center; justify-content: center;
    text-align: center;
    padding: 14px;
  }
  .front-badge .brand-name {
    font-weight: 800; font-size: 20px; line-height: 1.15;
    color: var(--brand-green-deep);
    letter-spacing: 0.02em;
  }
  /* Back */
  .card-back { background: var(--card-white); }
  .back-sweep { position: absolute; inset: 0; width: 100%; height: 100%; }
  .back-brand {
    position: absolute; left: 46px; top: 70px;
    display: flex; align-items: center; gap: 12px;
  }
  .back-brand .brand-mark {
    width: 26px; height: 26px; background: var(--brand-green-deep); border-radius: 3px;
  }
  .back-brand .brand-name {
    font-weight: 800; font-size: 22px; color: var(--ink);
    letter-spacing: 0.03em; line-height: 1;
  }
  .holder { position: absolute; left: 46px; top: 130px; }
  .holder-name {
    font-weight: 700; font-size: 27px; color: var(--brand-green-deep);
  }
  .holder-role {
    display: inline-block; margin-top: 4px;
    font-size: 14px; font-weight: 500; color: var(--ink);
    border-bottom: 1.5px solid var(--ink); padding-bottom: 2px;
  }
  .address {
    margin-top: 14px; font-size: 13.5px; line-height: 1.35; color: var(--ink);
  }
  .contact-list { list-style: none; margin-top: 12px; }
  .contact-list li {
    display: flex; align-items: center; gap: 10px;
    font-size: 13.5px; line-height: 1.55; color: var(--ink);
  }
  .contact-list svg { width: 13px; height: 13px; fill: var(--brand-green-deep); flex: none; }
</style>
</head>
<body>
<main class="stage">
  <section class="card card-front">
    <div class="front-pattern" role="img" aria-label="Repeating brand emblem pattern in green tones"></div>
    <div class="front-badge"><span class="brand-name">NORTHGATE BUILDERS</span></div>
  </section>

  <section class="card card-back">
    <svg class="back-sweep" viewBox="0 0 620 354" preserveAspectRatio="none" aria-hidden="true">
      <path d="M392 0 C380 140 460 250 620 262 L620 0 Z" fill="var(--brand-green)"/>
      <path d="M404 0 C394 134 470 236 620 248 L620 0 Z" fill="var(--night)"/>
    </svg>

    <div class="back-brand">
      <span class="brand-mark"></span>
      <span class="brand-name">NORTHGATE BUILDERS</span>
    </div>

    <div class="holder">
      <h1 class="holder-name">Daniel Corven</h1>
      <span class="holder-role">Owner</span>
      <p class="address">418 Maple Ridge Ave, #112<br>Fairview, OH 43150</p>
      <ul class="contact-list">
        <li><svg viewBox="0 0 24 24"><path d="M6.6 10.8a15.1 15.1 0 0 0 6.6 6.6l2.2-2.2a1 1 0 0 1 1-.25 11.4 11.4 0 0 0 3.6.57 1 1 0 0 1 1 1V20a1 1 0 0 1-1 1A17 17 0 0 1 3 4a1 1 0 0 1 1-1h3.5a1 1 0 0 1 1 1c0 1.25.2 2.45.57 3.57a1 1 0 0 1-.25 1z"/></svg>877-555-0142</li>
        <li><svg viewBox="0 0 24 24"><path d="M7 1h10a2 2 0 0 1 2 2v18a2 2 0 0 1-2 2H7a2 2 0 0 1-2-2V3a2 2 0 0 1 2-2zm0 3v14h10V4zm5 15.5a1.2 1.2 0 1 0 0 2.4 1.2 1.2 0 0 0 0-2.4z"/></svg>877-555-0187</li>
        <li><svg viewBox="0 0 24 24"><path d="M2 5h20v14H2zm2 2v.5l8 5 8-5V7z"/></svg>info@northgatebuilders.com</li>
        <li><svg viewBox="0 0 24 24"><circle cx="12" cy="12" r="10"/></svg>www.northgatebuilders.com</li>
      </ul>
    </div>
  </section>
</main>
</body>
</html>
```